Wordpress Design Project - Leadership Guide Nest

Website Brief

We are looking to have a design produced for a modern professional website. A mind map of the site can be found here: http://www.thoughtlattice.example/view.htm?m=58142736a1b94c07d2e5f8a3c6b71d09

Each of the green tabs are pages just next to them is a very small green globe. If you click this. It will take you through to an example page for that section.

Task description
The website will be made up of:
1. A homepage (this will be the blog see http://www.janetquillby.example for an example of the crisp and cleanness we are looking for)
2. A page that will have just a video and option page (see: http://tvpgacademy.example/ for example)
3. 3 pages all with the same structure. (see: http://tvpgacademy.example/qw72plx19bnv/ for an example). Each will have:
a. A video
b. Tabs at the top of the video that link to the 3 videos and the sales page
c. Link to a resource download
d. Friendline Comments section
4. 2 Page with about the experts and about our company (same style for both)
5. A page that will have a long well designed sales page (see: http://tvpgacademy.example/early-enrollment-2013/ for an example)
6. A page with testimonials on it (see http://www.janetquillby.example/praise/)
7. A page that will describe the products, services and provision we will be offering
8. A page that will detail our involvement with charities and not for profits

Must Have
Edgey, crisp design, similar to Janet Quillbys. We would like the colours to match very well throughout the site and have a unique font (possibly manksans). We want it to have very clean integrations between copy and images with shadows on videos for example like with Janetquillbys page. We really love this design and would like this to be the inspiration for our site however it would need to certainly have a more executive feel to suit our target market.

We like the idea of some kind of circles, crisp clean lines, nice white space, simple design, corporate looking, communicates wealth/success/massive value. Based on the two logos of NDLTR and the Hub (see attached)

Target Market:
The target market includes intelligent, productive coaches, who are self employed or part of small firms. They are well educated, well read, socially conscious, and committed to making a profound difference with their clients...skilled at the actions of coaching, but not the business side. There will be a ratio of approximately 60% male / 40% female (really? The coaching industry is predominantly female, no?), with an age range of 40 to 60 years. English is our core language. Most will have secondary education and the salary range will be $90,000 to $400,000. We will have a global audience reach, although the primary markets will be North America, Europe and Australia/NZ.

Marketing Objective:
LGN will be an on-line resource for Executive Coaches. The intent of the design will be to present LGN to the world as a highly professional organization. The intent is not to characterize LGN as solely corporate, but will also incorporate elements of entrepreneurialism. We require the brand to incorporate these values:
• Trustworthy – you can trust us
• Professional – we are true professionals whose mission is to provide value to our clients
• Caring - Interested in our clients wellbeing – we are keenly interested in helping our clients build their knowledge, skills, and attitudes to be highly productive and successful
• Successful
• Knowledgeable – we have breadth and depth of knowledge in leadership
• World-class – we have a world-wide target market and, as such, need the brand to reflect a powerful and inclusive image
• Positive Energy - I would like the brand to have positive energy and very clean feng shui
• Prestige
• Massive Value
• Accessible
• Worldly/ Sophisticated
• Affordable
• Mission-critical

Details about the needs, wants, aspirations etc. of our target market
Executive coaches need a process and a system for creating opportunities to do the work they love with clients who are qualified to engage them and pay them. There is a scarcity mentality around their own finances, but ironically an abundance mentality for what's possible in the world and for their clients. They want to make a difference, they want to facilitate transformation, they want to be of deep service.

They aspire to make a decent living doing it! They need help bridging the gap between practitioner/service provider and financially successful entrepreneur/business owner/ leader. They also aspire to have it be easy, as it feels hard for them to generate the revenues they want to generate solely through coaching, so many turn to training, speaking, and other revenue streams.

Required assets to send through to web designer
1. Three blog posts. Each will have:
a. A video/audio
b. Summary of the points raised
c. Download (possibly slides)
2. A page that will have just a video and option page
a. Headline
b. Video
c. One paragraph summary of what we do
3. 3 launch videos. Here for each we will need
a. A video scripted and produced
b. Title for each
c. A resource download
4. Sales page
a. Video
b. Copy
i. Overview
ii. Content of course
iii. Guarentee
iv. Details of bonuses
v. Details of support
vi. Pricing broken down ($30,000 value = $2000)
c. Animated Gif
5. About the company and experts
a. Description of our company, it's vision, mission, purpose and core values.
b. Description of each of us,
i. our key facts and wows,
ii. a picture of us
iii. some interesting facts (giving personality)
iv. Lower down we will add in "Faculty" these will be any thought leaders we invite in to be part of the value delivery (will add to our credibility having such a strong team behind the project)
6. Testimonials
a. Testimonials from coaches from working with us
7. Products, services and provision we will be offering
a. A simple description of each of the key products/services we will be offering
i. Leadership Guide Sales
ii. Leadership Guide Marketing
iii. Leadership Guide Help
iv. Leadership Guide Roundtable
v. Leadership Guide Resources
a. List of the various charity work each of us have been involved with

Requirements
Must have
• Edgey, crisp design, similar to Janet Quillbys. We would like the colours to match very well throughout the site and have a unique font (possibly manksans). We want it to have very clean integrations between copy and images with shadows on videos for example like with Janetquillbys page. We really love this design and would like this to be the inspiration for our site however it would need to certainly have a more executive feel to suit our target market.

```html
<!DOCTYPE html>
<html lang="en">
<head>
<meta charset="utf-8">
<title>Leadership Guide Nest</title>
<link href="https://fonts.googleapis.com/css2?family=Dosis:wght@400;500&family=Ubuntu:ital,wght@0,400;0,500;1,400&display=swap" rel="stylesheet">
<style>
:root{
  --orange:#e8692e;
  --orange-light:#f9c86c;
  --band:#f6b74e;
  --green:#93c866;
  --green-dark:#5f9e35;
  --nav:#4a4b4d;
  --ink:#555;
  --muted:#888;
  --footer:#414141;
  --panel:#f3f3f3;
  --line:#dcdcdc;
  --fb-blue:#5b77ad;
}
*{box-sizing:border-box;margin:0;padding:0}
html,body{width:832px;height:1200px;overflow:hidden}
body{position:relative;font-family:"Ubuntu",sans-serif;color:var(--ink);background:#ececec}
.abs{position:absolute}
/* header */
.site-header{left:0;top:0;width:832px;height:114px;background:linear-gradient(#fdfdfd,#e7e7e7);border-bottom:1px solid #d0d0d0}
.brand{left:100px;top:18px;width:140px;text-align:center}
.brand-mark{width:46px;height:46px;border-radius:50%;background:var(--orange);margin:0 auto 12px}
.brand-name{font-size:11.5px;color:#9a9a9a}
.util-links{left:485px;top:16px;font-size:8px;color:#777;letter-spacing:.2px}
.util-links span{margin:0 3px;color:#aaa}
.search{left:590px;top:13px;width:152px;height:16px;border:1px solid #c7c7c7;border-radius:3px;background:#f8f8f8;font-size:7.5px;font-style:italic;color:#aaa;padding:3px 7px}
.search svg{position:absolute;right:4px;top:2px}
.main-nav{left:312px;top:64px;width:430px;height:33px;background:linear-gradient(#5a5b5d,#3f4042);border-radius:2px;display:flex;box-shadow:0 1px 2px rgba(0,0,0,.3)}
.main-nav .home{width:40px;background:var(--orange);display:flex;align-items:center;justify-content:center;border-radius:2px 0 0 2px}
.main-nav a{color:#eee;font-size:10.5px;text-decoration:none;display:flex;align-items:center;padding:0 11px;border-left:1px solid #2f3031}
/* hero */
.hero-band{left:0;top:114px;width:832px;height:273px;background:linear-gradient(90deg,#f3a93a,var(--orange-light) 50%,#f3a93a)}
.slider{left:90px;top:122px;width:652px;height:251px;background:#fff;padding:3px;box-shadow:0 1px 3px rgba(0,0,0,.25)}
.slide-photo{left:3px;top:3px;width:646px;height:245px;background:linear-gradient(180deg,#f4f4f4 0%,#d9d6d3 45%,#6d6a68 100%)}
.caption{left:3px;top:138px;width:526px;height:110px;background:rgba(30,30,30,.82)}
.caption h1{position:absolute;left:24px;top:5px;font-family:"Dosis",sans-serif;font-weight:400;font-size:22px;line-height:28px;color:var(--orange-light);white-space:nowrap}
.caption p{position:absolute;left:24px;top:31px;width:480px;font-size:8.8px;color:#f1f1f1;line-height:18.5px}
.btn{position:absolute;top:74px;height:25px;line-height:25px;font-size:10px;color:#fff;border-radius:2px;text-align:center;white-space:nowrap}
.btn-green{left:230px;width:103px;background:linear-gradient(#9ccf6d,#6ea944);color:#2e4f17}
.btn-orange{left:370px;width:147px;background:linear-gradient(#f58b4a,#de5a20)}
.or{position:absolute;left:345px;top:74px;line-height:25px;color:#fff;font-size:10px}
.slide-dots{left:623px;top:86px;width:26px;height:78px;background:#f0a43a;border-radius:4px 0 0 4px;display:flex;flex-direction:column;align-items:center;justify-content:space-around;padding:5px 0}
.slide-dots i{width:11px;height:11px;border-radius:50%;background:#8a6a2a}
.slide-dots i.on{background:#111}
/* cards */
.card{background:#fff;border:1px solid #dadada;border-radius:5px;box-shadow:0 1px 2px rgba(0,0,0,.06)}
.card-title{font-family:"Dosis",sans-serif;font-weight:400;color:var(--orange);font-size:17.5px;text-transform:uppercase;white-space:nowrap}
.blog{left:90px;top:408px;width:430px;height:700px}
.post{width:396px;height:193px;left:22px;background:var(--panel);border:1px solid var(--line)}
.ribbon{left:-9px;top:7px;width:303px;height:24px}
.ribbon span{position:absolute;left:16px;top:5px;font-size:11px;color:#333;white-space:nowrap}
.post-photo{left:8px;top:43px;width:134px;height:98px;border:3px solid #fff;box-shadow:0 0 0 1px #ccc}
.post-text{left:161px;top:43px;width:228px;font-size:8px;line-height:16px;color:#6b6b6b}
.read-more{left:161px;top:124px;font-size:8px;background:linear-gradient(#f9cd7a,#efa83b);border:1px solid #d8922d;color:#4a3410;padding:3px 8px;border-radius:9px;white-space:nowrap}
.share-bar{left:8px;top:152px;width:378px;height:32px;background:#fff;border:1px solid var(--line);display:flex;align-items:center;justify-content:flex-end;gap:4px;padding-right:10px;font-size:7px}
.share-bar b{font-weight:500;border:1px solid #c6c6c6;border-radius:2px;padding:1px 4px;background:#f5f5f5;color:#3b5998}
.share-bar em{font-style:normal;border:1px solid #ccc;padding:1px 4px;color:#333;background:#fff}
.share-bar .tw{color:#2a76a9}
.share-bar .pl{color:#c23b22}
.share-bar .sv{color:#c8232c;margin-left:6px}
.pager{font-size:8px;letter-spacing:.3px;white-space:nowrap}
/* sidebar */
.videos{left:534px;top:408px;width:208px;height:155px}
.video-frame{left:11px;top:33px;width:185px;height:113px;background:linear-gradient(135deg,#3a3430,#7c6f64 55%,#2d2925)}
.form{left:534px;top:573px;width:208px;height:231px}
.field{left:10px;width:184px;height:19px;border:1px solid #d4d4d4;background:linear-gradient(#f4f4f4,#fff);font-size:7.5px;color:#aaa;padding:4px 8px}
.submit{left:137px;top:201px;width:57px;height:17px;background:linear-gradient(#4a4a4a,#222);color:#fff;font-size:7.5px;border-radius:9px;text-align:center;line-height:13px;border:2px solid #cfcfcf}
.fb{left:534px;top:814px;width:208px;height:160px;overflow:hidden}
.fb-head{left:0;top:0;width:208px;height:29px;background:var(--fb-blue);padding:7px 10px;font-family:"Dosis",sans-serif;font-size:14.5px;color:#fff;text-transform:uppercase;white-space:nowrap}
.fb-small{font-size:7.5px;color:#555;white-space:nowrap}
.fb-avatar{width:35px;height:35px;background:linear-gradient(#9a9a9a,#5b5b5b)}
.testi{left:534px;top:984px;width:208px;height:124px}
.testi p{left:14px;top:34px;width:182px;font-size:8px;font-style:italic;line-height:14px;color:#555}
/* footer */
.site-footer{left:0;top:1122px;width:832px;height:78px;background:var(--footer)}
.foot-links{left:90px;top:25px;font-size:8.5px;color:#ccc;white-space:nowrap}
.foot-links span{margin:0 5px;color:#888}
.copyright{left:90px;top:42px;font-size:7.5px;color:#bbb;white-space:nowrap}
.copyright b{font-weight:400;color:var(--orange-light)}
.social{left:601px;top:24px;display:flex;gap:6px}
.social i{width:24px;height:24px;border-radius:50%;background:#d9d9d9;display:flex;align-items:center;justify-content:center}
</style>
</head>
<body>

<header class="site-header abs">
  <div class="brand abs">
    <div class="brand-mark"></div>
    <div class="brand-name">Leadership Guide Nest</div>
  </div>
  <div class="util-links abs">Login<span>|</span>Help<span>|</span>Support</div>
  <div class="search abs">Search keyword.....
    <svg width="11" height="11" viewBox="0 0 12 12"><circle cx="5" cy="5" r="3.6" fill="none" stroke="#333" stroke-width="1.6"/><line x1="7.6" y1="7.6" x2="11" y2="11" stroke="#333" stroke-width="2"/></svg>
  </div>
  <nav class="main-nav abs">
    <div class="home"><svg width="14" height="12" viewBox="0 0 14 12"><path d="M7 0L0 6h2v6h4V8h2v4h4V6h2z" fill="#fff"/></svg></div>
    <a>About Us</a><a>Work With Us</a><a>Testimonials</a><a>Giving Back</a><a>Contact Us</a>
  </nav>
</header>

<section class="hero-band abs"></section>
<div class="slider abs">
  <div class="slide-photo abs" role="img" aria-label="Group photo of smiling business professionals in suits"></div>
  <div class="caption abs">
    <h1>Welcome to Our Company!</h1>
    <p>Vestibulum vel metus sit amet turpis bibendum tincidunt vel sit amet quam. Pellentesque habitant morbi<br>tristique senectus et netus et malesuada fames ac turpis egestas.<br>Nunc consequat congue nulla eu imperdiet......</p>
    <span class="btn btn-green">READ MORE</span>
    <span class="or">OR</span>
    <span class="btn btn-orange">DOWNLOAD RESOURCES</span>
  </div>
  <div class="slide-dots abs"><i class="on"></i><i></i><i></i><i></i></div>
</div>

<main class="blog card abs">
  <h2 class="card-title abs" style="left:13px;top:11px">Recent Blog Post</h2>

  <article class="post abs" style="top:44px">
    <svg class="ribbon abs" viewBox="0 0 303 30" preserveAspectRatio="none" style="height:30px"><path d="M0 0h303l-14 12 14 12H0z" fill="var(--green)"/><path d="M0 24h9v6z" fill="var(--green-dark)"/></svg>
    <div class="ribbon abs"><span>Post Heading Goes Here !</span></div>
    <div class="post-photo abs" role="img" aria-label="Businessman presenting a chart to a colleague" style="background:linear-gradient(135deg,#e9eef1,#b9c4cc 60%,#4b5660)"></div>
    <p class="post-text abs">Aliquam molestie, mi et imperdiet euismod, dui purus auctor tellus, et interdum lacus lectus et ante. Sed accumsan sollicitudin sapien, sit amet adipiscing turpis gravida ac. In congue, neque ac lobortis volutpat, libero mauris varius mi, vitae suscipit ipsum ligula vitae risus.</p>
    <span class="read-more abs">Read More</span>
    <div class="share-bar abs"><b>Like</b><em>559</em><b class="tw">Share</b><em>393</em><b class="pl">+1</b><em>11</em><b class="sv">Save</b><em>5</em></div>
  </article>

  <article class="post abs" style="top:248px">
    <svg class="ribbon abs" viewBox="0 0 303 30" preserveAspectRatio="none" style="height:30px"><path d="M0 0h303l-14 12 14 12H0z" fill="var(--green)"/><path d="M0 24h9v6z" fill="var(--green-dark)"/></svg>
    <div class="ribbon abs"><span>Post Heading Goes Here !</span></div>
    <div class="post-photo abs" role="img" aria-label="Two smiling businesswomen" style="background:linear-gradient(135deg,#f6efe6,#d9b58c 55%,#8a6a4a)"></div>
    <p class="post-text abs">Aliquam molestie, mi et imperdiet euismod, dui purus auctor tellus, et interdum lacus lectus et ante. Sed accumsan sollicitudin sapien, sit amet adipiscing turpis gravida ac. In congue, neque ac lobortis volutpat, libero mauris varius mi, vitae suscipit ipsum ligula vitae risus.</p>
    <span class="read-more abs">Read More</span>
    <div class="share-bar abs"><b>Like</b><em>559</em><b class="tw">Share</b><em>393</em><b class="pl">+1</b><em>11</em><b class="sv">Save</b><em>5</em></div>
  </article>

  <article class="post abs" style="top:452px">
    <svg class="ribbon abs" viewBox="0 0 303 30" preserveAspectRatio="none" style="height:30px"><path d="M0 0h303l-14 12 14 12H0z" fill="var(--green)"/><path d="M0 24h9v6z" fill="var(--green-dark)"/></svg>
    <div class="ribbon abs"><span>Post Heading Goes Here !</span></div>
    <div class="post-photo abs" role="img" aria-label="Black and white portrait of three business colleagues" style="background:linear-gradient(135deg,#eaeaea,#9a9a9a 55%,#3a3a3a)"></div>
    <p class="post-text abs">Aliquam molestie, mi et imperdiet euismod, dui purus auctor tellus, et interdum lacus lectus et ante. Sed accumsan sollicitudin sapien, sit amet adipiscing turpis gravida ac. In congue, neque ac lobortis volutpat, libero mauris varius mi, vitae suscipit ipsum ligula vitae risus.</p>
    <span class="read-more abs">Read More</span>
    <div class="share-bar abs"><b>Like</b><em>559</em><b class="tw">Share</b><em>393</em><b class="pl">+1</b><em>11</em><b class="sv">Save</b><em>5</em></div>
  </article>

  <div class="pager abs" style="left:23px;top:674px;color:#888">&lt;-- PREVIOUS ENTRIES</div>
  <div class="pager abs" style="left:345px;top:674px;color:var(--orange)">NEW ENTRIES --&gt;</div>
</main>

<aside>
  <section class="videos card abs">
    <h2 class="card-title abs" style="left:11px;top:9px;font-size:15px">Our Videos</h2>
    <div class="video-frame abs" role="img" aria-label="Video still of business colleagues in conversation"></div>
    <svg class="abs" style="left:85px;top:67px" width="36" height="36" viewBox="0 0 36 36"><circle cx="18" cy="18" r="17" fill="rgba(255,255,255,.55)"/><path d="M14 10l12 8-12 8z" fill="#555"/></svg>
  </section>

  <section class="form card abs">
    <h2 class="card-title abs" style="left:10px;top:9px;font-size:15px">Fill Option Form</h2>
    <div class="field abs" style="top:36px">Full Name</div>
    <div class="field abs" style="top:60px">Contact No.</div>
    <div class="field abs" style="top:85px">Email Address</div>
    <div class="field abs" style="top:110px;height:79px">Message</div>
    <div class="submit abs">SUBMIT</div>
  </section>

  <section class="fb card abs">
    <div class="fb-head abs">Friendline Comments</div>
    <div class="abs" style="left:11px;top:37px;width:30px;height:30px;border:1px solid #ddd;display:flex;align-items:center;justify-content:center"><i style="width:12px;height:12px;border-radius:50%;background:var(--orange)"></i></div>
    <div class="fb-small abs" style="left:50px;top:37px"><b style="font-weight:500;color:#3b5998">Leadership Guide Nest</b> <span style="color:#3b5998">on Friendline</span></div>
    <div class="abs" style="left:50px;top:52px;font-size:7px;border:1px solid #b8c2d6;background:#eef1f7;color:#3b5998;padding:1px 5px">Like</div>
    <div class="fb-small abs" style="left:11px;top:75px">2,081 people like <b style="font-weight:500">Leadership Guide Nest</b></div>
    <div class="fb-avatar abs" role="img" aria-label="Profile picture" style="left:11px;top:90px"></div>
    <div class="fb-avatar abs" role="img" aria-label="Profile picture" style="left:60px;top:90px;background:linear-gradient(#9fb8cf,#7a5a3a)"></div>
    <div class="fb-avatar abs" role="img" aria-label="Profile picture" style="left:109px;top:90px;background:linear-gradient(#4a6a8a,#222)"></div>
    <div class="fb-small abs" style="left:18px;top:128px;font-size:6.5px">Omar</div>
    <div class="fb-small abs" style="left:55px;top:128px;font-size:6.5px">Nadia Farooq</div>
    <div class="fb-small abs" style="left:117px;top:128px;font-size:6.5px">Zeno</div>
    <div class="abs" style="left:0;top:138px;width:208px;border-top:1px solid #ddd"></div>
    <i class="abs" style="left:13px;top:144px;width:12px;height:12px;background:var(--fb-blue)"></i>
    <div class="fb-small abs" style="left:32px;top:146px;font-size:6px;letter-spacing:.8px">Friendline Plugins</div>
  </section>

  <section class="testi card abs">
    <h2 class="card-title abs" style="left:13px;top:10px;font-size:15px">Testimonials</h2>
    <svg class="abs" style="left:18px;top:37px" width="18" height="11" viewBox="0 0 18 11"><path d="M5 0h4L4 11H0zM13 0h4l-5 11H8z" fill="#9a9a9a"/></svg>
    <p class="abs"><span style="padding-left:24px"></span>Nam fermentum vestibulum purus id aliquet. Phasellus dui ante, ultricies et sollicitudin pretium, fermentum vel velit.....</p>
    <div class="abs" style="left:14px;top:86px;font-size:7.5px;font-style:italic;color:#e59a3a">Continue Reading</div>
    <div class="abs" style="right:13px;top:96px;font-size:7.5px;font-style:italic;font-weight:500;color:var(--orange)">By Harold Penwick</div>
    <div class="abs" style="right:13px;top:107px;font-size:7.5px;font-style:italic;color:#888">Posted on Dec 01, 2012</div>
  </section>
</aside>

<footer class="site-footer abs">
  <div class="foot-links abs">Home<span>|</span>About Us<span>|</span>Work With Us<span>|</span>Testimonials<span>|</span>Contact Us</div>
  <div class="copyright abs">© 2012 by <b>LeadershipGuideNest</b>. All Right Reserved</div>
  <div class="social abs">
    <i><svg width="12" height="12" viewBox="0 0 12 12"><circle cx="2" cy="10" r="1.6" fill="#414141"/><path d="M1 5a6 6 0 0 1 6 6M1 1a10 10 0 0 1 10 10" fill="none" stroke="#414141" stroke-width="1.8"/></svg></i>
    <i><svg width="13" height="9" viewBox="0 0 13 9"><rect width="13" height="9" rx="1" fill="#414141"/><path d="M0 0l6.5 5L13 0" fill="none" stroke="#d9d9d9" stroke-width="1"/></svg></i>
    <i></i><i></i><i></i>
  </div>
</footer>

</body>
</html>
```